Velorin Wine Label For Canopy Haven

Lantern Brook Winery is in need of a wine label for new wine being release. This wine will be used as a fundraiser for Canopy Haven, a chimpanzee santuary in Georgia. The label should reflect a high-end, classy image and the label should suggest the chimp philanthropy without specifically naming the organization (for legal purposes). The label can be a little whimsical without being too cartoonish or child like. This wine will be sold for $30 so it should project a sense of elegance too.
Updates

holiday season makes it difficult to get feedback necessary for approval. just need a few more days...

Industry/Entity Type

Winery

Font styles to use
Sans Serif

Requirements
Must have
• Label should show common design appearance as other labels downloaded.
• Label should be a dark (emerald) green color. Label should have wine name "Velorin" in center. Label should include an image or silhouette of a chimp on it
Should not have
• no cartoonish images;

```html
<!DOCTYPE html>
<html lang="en">
<head>
<meta charset="utf-8">
<title>Velorin — Lantern Brook Winery</title>
<link href="https://fonts.googleapis.com/css2?family=Cinzel:wght@400;600&display=swap" rel="stylesheet">
<style>
  :root {
    --backdrop: #2e6450;
    --backdrop-deep: #1f4a39;
    --label-paper: #cfe6da;
    --label-paper-light: #dcefe5;
    --emerald: #1f7a5c;
    --emerald-dark: #16604a;
    --portrait-tone: #4a4f4c;
    --portrait-light: #9aa39e;
  }
  html, body {
    margin: 0;
    padding: 0;
    width: 1200px;
    height: 1200px;
    overflow: hidden;
  }
  body {
    background: radial-gradient(circle at 50% 40%, var(--backdrop) 0%, var(--backdrop-deep) 100%);
  }
  .wine-label {
    display: block;
    width: 1200px;
    height: 1200px;
  }
  .label-paper { fill: var(--label-paper); }
  .diamond-fill { fill: var(--label-paper-light); }
  .diamond-outer { fill: none; stroke: var(--emerald); stroke-width: 6; }
  .diamond-inner { fill: none; stroke: var(--emerald); stroke-width: 2.5; }
  .wine-name {
    font-family: "Cinzel", serif;
    font-weight: 400;
    font-size: 84px;
    letter-spacing: 3px;
    fill: var(--emerald-dark);
  }
  .winery-name {
    font-family: "Cinzel", serif;
    font-weight: 600;
    font-size: 36px;
    letter-spacing: 3px;
    fill: var(--emerald);
  }
  .winery-sub {
    font-family: "Cinzel", serif;
    font-weight: 600;
    font-size: 24px;
    letter-spacing: 4px;
    fill: var(--emerald);
  }
  .spec-text {
    font-family: "Cinzel", serif;
    font-size: 20px;
    letter-spacing: 1px;
    fill: var(--emerald-dark);
  }
</style>
</head>
<body>
<svg class="wine-label" viewBox="0 0 1200 1200" xmlns="http://www.w3.org/2000/svg">
  <defs>
    <radialGradient id="portraitTone" cx="50%" cy="50%" r="55%">
      <stop offset="0%" stop-color="var(--portrait-tone)"/>
      <stop offset="100%" stop-color="var(--portrait-light)" stop-opacity="0.6"/>
    </radialGradient>
  </defs>

  <rect class="label-paper" x="100" y="380" width="1000" height="520"/>

  <polygon class="diamond-fill" points="600,250 900,640 600,1030 300,640"/>
  <polygon class="diamond-outer" points="600,250 900,640 600,1030 300,640"/>
  <polygon class="diamond-inner" points="600,275 880,640 600,1005 320,640"/>

  <ellipse class="portrait" role="img" aria-label="Engraved profile portrait of a chimpanzee" cx="600" cy="510" rx="135" ry="100" fill="url(#portraitTone)"/>

  <text class="wine-name" x="600" y="700" text-anchor="middle">VELORIN</text>

  <text class="winery-name" x="600" y="752" text-anchor="middle">LANTERN</text>
  <text class="winery-sub" x="600" y="790" text-anchor="middle">· BROOK ·</text>

  <text class="spec-text" x="150" y="820">13% Alc/Vol</text>
  <text class="spec-text" x="1050" y="820" text-anchor="end">750mL</text>
</svg>
</body>
</html>
```